Stickers By Dwayne needs a website and logo design

I am starting a home business, "Stickers By Dwayne", which I will sell car decals/decals of some sort. I am looking for a creative and professional looking website. I do not want anything too plain/bland, or else I could design it myself. I am up for many options, when it comes to text/colors, and I am not opposed to much. Just nothing too plain. Currently have no logo design to use, may also add this to the project as well. ( I use Wordpress for my site server so it has to be compatible to be used with that website.
Also, I make decals that mainly go on car windows, not as big on car body’s. Also put decals on glassware, and other items. But mainly car windows

• some color, not be bland and white everywhere.

```html
<!DOCTYPE html>
<html lang="en">
<head>
<meta charset="utf-8">
<title>Stickers By Dwayne</title>
<link rel="stylesheet" href="https://fonts.googleapis.com/css2?family=Oswald:wght@400;500;600&family=Open+Sans:ital,wght@0,400;0,600;0,700;1,600&display=swap">
<style>
:root{
  --orange:#f7931e;
  --orange-deep:#e5780c;
  --orange-light:#fbb040;
  --dark:#1d1d1d;
  --darker:#121212;
  --footer:#0d0d0d;
  --white:#ffffff;
  --muted:#d6d6d6;
  --ring:#3a3a3a;
}
*{margin:0;padding:0;box-sizing:border-box}
html,body{width:1200px;height:2839px;overflow:hidden}
body{position:relative;background:var(--dark);color:var(--white);font-family:"Open Sans",Arial,sans-serif}
.abs{position:absolute}
.heading{font-family:"Oswald",Impact,sans-serif;font-weight:500;text-transform:uppercase;letter-spacing:.5px}

/* hero */
.hero{position:absolute;left:0;top:0;width:1200px;height:530px;overflow:hidden}
.hero-photo{position:absolute;inset:0;background:linear-gradient(100deg,#6f6f66 0%,#8c8b82 30%,#77806a 55%,#4f5e3c 80%,#3f4d2f 100%)}
.hero-shade{position:absolute;inset:0;background:linear-gradient(90deg,rgba(0,0,0,.45) 0%,rgba(0,0,0,.15) 50%,rgba(0,0,0,0) 100%)}
.brand{left:98px;top:30px;font-size:27px;font-family:"Oswald",sans-serif;font-weight:600;text-transform:uppercase;letter-spacing:.3px}
.nav{left:379px;top:38px;display:flex;gap:22px;font-family:"Oswald",sans-serif;font-size:15px}
.nav-tools{left:974px;top:31px;display:flex;gap:10px}
.tool{width:36px;height:36px;border:2px solid var(--white);border-radius:50%;display:flex;align-items:center;justify-content:center}
.tool.cart{background:var(--orange);border-color:var(--orange)}
.hero-title{left:98px;top:186px;font-size:64px;line-height:1;font-family:"Oswald",sans-serif;font-weight:600;text-transform:uppercase}
.hero-sub{left:100px;top:270px;font-size:22px;font-style:italic;font-weight:600}
.btn{left:98px;top:324px;width:196px;height:47px;border-radius:24px;background:var(--orange);border:2px solid #fff3;color:var(--white);font-family:"Oswald",sans-serif;font-size:16px;display:flex;align-items:center;justify-content:center;text-transform:uppercase}
.dots{left:566px;top:464px;display:flex;gap:5px}
.dots span{width:13px;height:13px;border:2px solid var(--white);border-radius:50%}
.dots span.on{background:var(--white)}

/* welcome */
.welcome{position:absolute;left:0;top:530px;width:1200px;height:549px;background:var(--dark)}
.section-title{position:absolute;left:0;width:1200px;text-align:center;font-size:35px}
.intro{position:absolute;left:285px;width:630px;text-align:center;font-size:14px;line-height:26px;color:var(--muted)}
.service{position:absolute;width:240px;text-align:center}
.ring{width:146px;height:146px;margin:0 auto;border-radius:50%;border:2px solid #555;display:flex;align-items:center;justify-content:center}
.ring-inner{width:126px;height:126px;border-radius:50%;background:var(--ring);display:flex;align-items:center;justify-content:center}
.service h3{margin-top:36px;font-family:"Oswald",sans-serif;font-weight:500;font-size:20px}
.service p{margin-top:12px;font-size:12.5px;line-height:24px;color:var(--muted)}

/* products */
.products{position:absolute;left:0;top:1079px;width:1200px;height:606px;background:linear-gradient(160deg,var(--orange-light) 0%,var(--orange) 45%,var(--orange-deep) 100%)}
.product{position:absolute;top:161px;width:233px}
.product-photo{width:233px;height:193px;border:3px solid var(--white)}
.product h3{margin-top:27px;font-family:"Oswald",sans-serif;font-weight:500;font-size:19px}
.product p{margin-top:10px;font-size:12.5px;line-height:21px;color:#fff3e0}
.more{margin-top:17px;font-size:12.5px;font-weight:700;text-transform:uppercase}
.arrow{position:absolute;top:255px;width:42px;height:42px;border:2px solid var(--white);border-radius:50%;display:flex;align-items:center;justify-content:center}

/* blog */
.blog{position:absolute;left:0;top:1685px;width:1200px;height:583px;background:var(--darker)}
.post{position:absolute;top:155px;width:324px}
.post-photo{width:324px;height:184px;border:3px solid var(--white)}
.post h3{margin-top:28px;font-family:"Oswald",sans-serif;font-weight:500;font-size:19px}
.meta{margin-top:12px;font-size:12.5px;display:flex;align-items:center;gap:6px}
.meta .sep{margin:0 6px}
.post p{margin-top:12px;font-size:12.5px;line-height:22px;color:var(--muted)}
.post .more{color:var(--orange);margin-top:16px}

/* feed strip */
.feed{position:absolute;left:0;top:2268px;width:1200px;height:218px;border-top:4px solid var(--orange);border-bottom:4px solid var(--orange);display:flex;background:var(--orange);gap:4px}
.feed-tile{flex:1}
.feed-label{position:absolute;left:522px;top:2351px;width:160px;height:50px;background:rgba(0,0,0,.78);display:flex;align-items:center;justify-content:center;gap:10px;font-family:"Oswald",sans-serif;font-size:17px;font-weight:500;text-transform:uppercase}

/* footer */
.footer{position:absolute;left:0;top:2486px;width:1200px;height:353px;background:var(--footer)}
.footer-brand{left:98px;top:68px;font-family:"Oswald",sans-serif;font-weight:500;font-size:26px;text-transform:uppercase}
.footer-about{left:98px;top:114px;width:270px;font-size:13px;line-height:24px;color:var(--muted)}
.socials{left:98px;top:206px;display:flex;gap:8px}
.socials span{width:23px;height:23px;border-radius:50%}
.col{position:absolute;top:56px}
.col h4{font-family:"Oswald",sans-serif;font-weight:500;font-size:18px;text-transform:uppercase}
.col ul{list-style:none;margin-top:18px}
.col li{font-size:12px;line-height:30px;color:var(--muted)}
.copyright{left:98px;top:308px;font-size:11.5px;color:var(--muted)}
.cards{left:882px;top:299px;display:flex;gap:6px}
.cards span{width:51px;height:34px;background:var(--white);border-radius:3px;color:#1d3a8a;font-size:10px;font-weight:700;display:flex;align-items:center;justify-content:center}
</style>
</head>
<body>

<header class="hero">
  <div class="hero-photo" role="img" aria-label="Photo of a silver rally car with orange racing stripes on a forest road"></div>
  <div class="hero-shade"></div>
  <div class="abs brand">Stickers By Dwayne</div>
  <nav class="abs nav"><span>Home</span><span>About</span><span>Products</span><span>Inspiration</span><span>Shop</span><span>Build your own</span><span>Blog</span><span>Contact</span></nav>
  <div class="abs nav-tools">
    <div class="tool"><svg width="16" height="16" viewBox="0 0 16 16"><circle cx="6.5" cy="6.5" r="4.5" fill="none" stroke="#fff" stroke-width="2"/><line x1="10" y1="10" x2="14" y2="14" stroke="#fff" stroke-width="2.4"/></svg></div>
    <div class="tool"><svg width="16" height="16" viewBox="0 0 16 16"><circle cx="8" cy="5" r="3.4" fill="#fff"/><path d="M2 15c0-4 3-6 6-6s6 2 6 6z" fill="#fff"/></svg></div>
    <div class="tool cart"><svg width="18" height="16" viewBox="0 0 18 16"><path d="M1 2h3l2 8h9l2-6H5" fill="none" stroke="#fff" stroke-width="1.8"/><circle cx="7" cy="13.5" r="1.5" fill="#fff"/><circle cx="14" cy="13.5" r="1.5" fill="#fff"/></svg></div>
  </div>
  <h1 class="abs hero-title">Stickers By Dwayne</h1>
  <p class="abs hero-sub">Selling car decals/decals of some sort</p>
  <div class="abs btn">Get more info</div>
  <div class="abs dots"><span class="on"></span><span></span><span></span><span></span></div>
</header>

<section class="welcome">
  <h2 class="heading section-title" style="top:68px">Welcome to Stickers By Dwayne</h2>
  <p class="intro" style="top:124px">Nemo enim ipsam voluptatem quia voluptas sit aspernatur aut odit aut fugit, sed quia consequuntur magni dolores eos qui ratione voluptatem sequi ne uisquam est, qui dolorem ipsum.</p>

  <div class="service" style="left:83px;top:213px">
    <div class="ring"><div class="ring-inner">
      <svg width="52" height="52" viewBox="0 0 52 52"><rect x="5" y="10" width="34" height="34" rx="5" fill="none" stroke="#f7931e" stroke-width="4"/><path d="M20 34l2-8 18-18 6 6-18 18z" fill="#f7931e"/></svg>
    </div></div>
    <h3>Design</h3><p>Nemo enim ipsam volupta quia vol uptas sit aspernatur aut odita</p>
  </div>
  <div class="service" style="left:346px;top:213px">
    <div class="ring"><div class="ring-inner">
      <svg width="52" height="52" viewBox="0 0 52 52"><path d="M10 24a16 16 0 0 1 29-9" fill="none" stroke="#f7931e" stroke-width="6"/><path d="M44 6v14H30z" fill="#f7931e"/><path d="M42 28a16 16 0 0 1-29 9" fill="none" stroke="#f7931e" stroke-width="6"/><path d="M8 46V32h14z" fill="#f7931e"/></svg>
    </div></div>
    <h3>Restyling</h3><p>Nemo enim ipsam volupta quia vol uptas sit aspernatur aut odita</p>
  </div>
  <div class="service" style="left:611px;top:213px">
    <div class="ring"><div class="ring-inner">
      <svg width="54" height="48" viewBox="0 0 54 48"><rect x="3" y="3" width="48" height="42" rx="4" fill="none" stroke="#f7931e" stroke-width="4"/><circle cx="16" cy="15" r="5" fill="#f7931e"/><path d="M9 39l12-13 7 7 9-11 9 17z" fill="#f7931e"/></svg>
    </div></div>
    <h3>Wrapping</h3><p>Nemo enim ipsam volupta quia vol uptas sit aspernatur aut odita</p>
  </div>
  <div class="service" style="left:874px;top:213px">
    <div class="ring"><div class="ring-inner">
      <svg width="52" height="52" viewBox="0 0 52 52"><line x1="12" y1="4" x2="12" y2="42" stroke="#f7931e" stroke-width="4"/><path d="M4 38h16l-8 11z" fill="#f7931e"/><text x="36" y="22" font-family="Oswald,sans-serif" font-size="20" fill="#f7931e" text-anchor="middle">A</text><text x="36" y="47" font-family="Oswald,sans-serif" font-size="20" fill="#f7931e" text-anchor="middle">Z</text></svg>
    </div></div>
    <h3>Lettering</h3><p>Nemo enim ipsam volupta quia vol uptas sit aspernatur aut odita</p>
  </div>
</section>

<section class="products">
  <h2 class="heading section-title" style="top:70px">Our Products</h2>
  <div class="arrow" style="left:41px"><svg width="12" height="14" viewBox="0 0 12 14"><path d="M9 1L3 7l6 6" fill="none" stroke="#fff" stroke-width="2"/></svg></div>
  <div class="arrow" style="left:1114px"><svg width="12" height="14" viewBox="0 0 12 14"><path d="M3 1l6 6-6 6" fill="none" stroke="#fff" stroke-width="2"/></svg></div>

  <article class="product" style="left:98px">
    <div class="product-photo" role="img" aria-label="White sports car with a window decal" style="background:linear-gradient(135deg,#e9e9e9,#9a9a9a 60%,#3a3a3a)"></div>
    <h3>Car Window Decals</h3><p>Nam libero tempore, cum soluta nobis est eligendi optio cumque nihil imquo minus id quod maxim.</p><div class="more">Read more</div>
  </article>
  <article class="product" style="left:354px">
    <div class="product-photo" role="img" aria-label="Black car with price lettering on the windscreen" style="background:linear-gradient(180deg,#8aa0a6,#2d2d2d 55%,#5f8a3a)"></div>
    <h3>Car Lettering</h3><p>Nam libero tempore, cum soluta nobis est eligendi optio cumque nihil imquo minus id quod maxim.</p><div class="more">Read more</div>
  </article>
  <article class="product" style="left:611px">
    <div class="product-photo" role="img" aria-label="Off-road vehicle covered in decals on a street" style="background:linear-gradient(180deg,#b9b3a6,#3a3a3a 60%,#6d6a64)"></div>
    <h3>Car Decals</h3><p>Nam libero tempore, cum soluta nobis est eligendi optio cumque nihil imquo minus id quod maxim.</p><div class="more">Read more</div>
  </article>
  <article class="product" style="left:867px">
    <div class="product-photo" role="img" aria-label="SUV in a camouflage wrap" style="background:linear-gradient(180deg,#7f9a6b,#a9aab0 55%,#5d5d60)"></div>
    <h3>Car Window Stickers</h3><p>Nam libero tempore, cum soluta nobis est eligendi optio cumque nihil imquo minus id quod maxim.</p><div class="more">Read more</div>
  </article>
</section>

<section class="blog">
  <h2 class="heading section-title" style="top:70px">Latest Blog</h2>
  <article class="post" style="left:98px">
    <div class="post-photo" role="img" aria-label="Blue hatchback with red side graphics outside a showroom" style="background:linear-gradient(180deg,#9fb6c4,#1f3f8a 60%,#777)"></div>
    <h3>Finibus Bonorumet Maloru</h3>
    <div class="meta"><svg width="12" height="12" viewBox="0 0 12 12"><rect x="1" y="2" width="10" height="9" fill="none" stroke="#f7931e" stroke-width="1.5"/><line x1="1" y1="5" x2="11" y2="5" stroke="#f7931e" stroke-width="1.5"/></svg>25/09/2017<span class="sep">|</span><svg width="11" height="12" viewBox="0 0 11 12"><circle cx="5.5" cy="3.5" r="3" fill="#f7931e"/><path d="M0 12c0-4 2.5-5 5.5-5s5.5 1 5.5 5z" fill="#f7931e"/></svg>Marcus</div>
    <p>Neque porro quisquam est, qui dolorem ipsqu ia dolor sit amet, consectetur, adipisci.</p><div class="more">Read more</div>
  </article>
  <article class="post" style="left:437px">
    <div class="post-photo" role="img" aria-label="White car door with a blue fleet map wrap" style="background:linear-gradient(180deg,#b7c7d4,#e6e8ea 55%,#6a6a6a)"></div>
    <h3>Finibus Bonorumet Maloru</h3>
    <div class="meta"><svg width="12" height="12" viewBox="0 0 12 12"><rect x="1" y="2" width="10" height="9" fill="none" stroke="#f7931e" stroke-width="1.5"/><line x1="1" y1="5" x2="11" y2="5" stroke="#f7931e" stroke-width="1.5"/></svg>25/09/2017<span class="sep">|</span><svg width="11" height="12" viewBox="0 0 11 12"><circle cx="5.5" cy="3.5" r="3" fill="#f7931e"/><path d="M0 12c0-4 2.5-5 5.5-5s5.5 1 5.5 5z" fill="#f7931e"/></svg>Marcus</div>
    <p>Neque porro quisquam est, qui dolorem ipsqu ia dolor sit amet, consectetur, adipisci.</p><div class="more">Read more</div>
  </article>
  <article class="post" style="left:776px">
    <div class="post-photo" role="img" aria-label="Red vintage estate car with flower stickers" style="background:linear-gradient(180deg,#3b3b3b,#b3242b 55%,#8a8a8a)"></div>
    <h3>Finibus Bonorumet Maloru</h3>
    <div class="meta"><svg width="12" height="12" viewBox="0 0 12 12"><rect x="1" y="2" width="10" height="9" fill="none" stroke="#f7931e" stroke-width="1.5"/><line x1="1" y1="5" x2="11" y2="5" stroke="#f7931e" stroke-width="1.5"/></svg>25/09/2017<span class="sep">|</span><svg width="11" height="12" viewBox="0 0 11 12"><circle cx="5.5" cy="3.5" r="3" fill="#f7931e"/><path d="M0 12c0-4 2.5-5 5.5-5s5.5 1 5.5 5z" fill="#f7931e"/></svg>Marcus</div>
    <p>Neque porro quisquam est, qui dolorem ipsqu ia dolor sit amet, consectetur, adipisci.</p><div class="more">Read more</div>
  </article>
</section>

<section class="feed">
  <div class="feed-tile" role="img" aria-label="Hands applying wrap film" style="background:linear-gradient(135deg,#777,#1e1e1e)"></div>
  <div class="feed-tile" role="img" aria-label="Drift car with graphic livery" style="background:linear-gradient(180deg,#8d8d8d,#2a2a2a 60%,#b0b0b0)"></div>
  <div class="feed-tile" role="img" aria-label="Blue rally car" style="background:linear-gradient(180deg,#6a7f8a,#1f3f9a 60%,#d4a92a)"></div>
  <div class="feed-tile" role="img" aria-label="Teal rally car on track" style="background:linear-gradient(180deg,#7fa26a,#6cb7b0 55%,#777)"></div>
  <div class="feed-tile" role="img" aria-label="Red car window with wedding lettering" style="background:linear-gradient(135deg,#d63a2b,#8a1a14)"></div>
</section>
<div class="feed-label"><svg width="16" height="16" viewBox="0 0 16 16"><rect x="1" y="1" width="14" height="14" rx="3" fill="none" stroke="#fff" stroke-width="2"/></svg>Picfeed</div>

<footer class="footer">
  <div class="abs footer-brand">Stickers By Dwayne</div>
  <p class="abs footer-about">Nam libero tempore, cum soluta nobis est eligendi optio cumque nihil impedit quimi nus id quod maxime plac.</p>
  <div class="abs socials">
    <span style="background:#3fb37f"></span><span style="background:#3b5998"></span><span style="background:#1da1f2"></span><span style="background:#dd4b39"></span><span style="background:#3f729b"></span><span style="background:#5aa0d6"></span><span style="background:#e62117"></span><span style="background:#cb2027"></span>
  </div>
  <div class="col" style="left:441px"><h4>Information</h4><ul><li>About Us</li><li>Careers</li><li>Privacy &amp; Security</li><li>Site Map</li><li>Terms of Use</li><li>Blog</li></ul></div>
  <div class="col" style="left:670px"><h4>Help &amp; Support</h4><ul><li>Recommended Reading</li><li>Submit your Story</li><li>Contact Us</li><li>Frequently Asked Questions</li><li>How to Order</li></ul></div>
  <div class="col" style="left:935px"><h4>My Account</h4><ul><li>Delivery Information</li><li>My Account</li><li>Order Tracking</li><li>Reminder Service</li><li>Shipping, Returns &amp; Fees</li></ul></div>
  <p class="abs copyright">Copyright © 2017, Stickers By Dwayne. - All Rights Reserved.</p>
  <div class="abs cards"><span>Cardo</span><span>Payly</span><span>Roam</span><span>Expressa</span></div>
</footer>

</body>
</html>
```